Brightwell Aero Services Logo

I need a website and logo for the parent company Brightwell Aero Services, which encompasses general aviation aircraft repair, small aircrat rental and flight school. The company is based in Lawrenceville, Georgia at the Tolleson county airport. A saying that can be incorporated somehere could be, "Quality flying is safe flying", "Safety in mind is no accident" ,. I need a website and logo.

The company started as a repair shop performing repairs and inspections on Harlan, Vantor, Delkin and Ralstead general aviation aircraft, all models of single engine piston, multi engine piston, and single engine turboprop with an emphasis on Harlan Solvane and AeroTurn turbo prop aircraft. We have se=ince entered the aircraft rental and flight instruction market using the Delkin 240 ang Harlan Ranger aircraft.

Number of Pages; I don't know. Maybe 5 ? A home page for Brightwell Aero Services, page for maintenance and repairs and a couple for the rental and school. The maintenance shop is busy, always has been. I need to get the rental and school advertised and busy.

I have a logo for the maintenance shop shirts, not for the school. I do not have the file. I paid a business locally to do that and print on the shirts. They have the file.

Target Market(s)

In our flight school rental fleet department, we are looking for persons wishing to obtain their private pilot license and continuing on into their commercial and instrument ratings. In the aircraft maintenance department, we are looking for new customers who want a better and more quality relationship with their aircraft maintenance provider who will give more detail and quality in the repairs with an emphasis on safety and fewer problems between scheduled maintenance cycles on their aircraft. Brightwell's owner, Dale Hutchins, has been performing aircraft maintenance in the Atlanta area for 27 years. He has built a steady customer base through those years.

```html
<!DOCTYPE html>
<html lang="en">
<head>
<meta charset="utf-8">
<title>Brightwell Aero Services</title>
<link href="https://fonts.googleapis.com/css2?family=Oswald:wght@400;500;600&family=Poppins:wght@400;500;600&display=swap" rel="stylesheet">
<style>
:root{
  --blue:#1f7bc1;
  --blue-dark:#16629c;
  --orange:#ff6a00;
  --ink:#1c1c1c;
  --text:#444;
  --light:#f2f4f7;
  --footer:#232323;
  --white:#fff;
}
*{box-sizing:border-box;margin:0;padding:0}
html,body{width:1200px;height:4158px;overflow:hidden;background:var(--white)}
body{font-family:'Poppins',sans-serif;color:var(--text);position:relative}
.abs{position:absolute}
.heading{font-family:'Oswald',sans-serif;font-weight:500;color:var(--ink);text-transform:uppercase;font-size:31px;letter-spacing:.2px}
.heading span{color:var(--blue)}
.underline{display:block;width:106px;height:3px;background:var(--orange);margin-top:6px}
.center{text-align:center}
.center .underline{margin-left:auto;margin-right:auto}
.body-text{font-size:14px;line-height:25px}
.btn{position:absolute;background:var(--orange);color:var(--white);font-family:'Oswald',sans-serif;font-size:14px;font-weight:500;display:flex;align-items:center;justify-content:center;text-transform:uppercase}

/* brand */
.brand{display:flex;align-items:center;gap:10px;color:var(--white);font-family:'Oswald',sans-serif;font-weight:400;line-height:1.15}
.brand-mark{background:var(--white);flex:none}

/* header + hero */
.hero{left:0;top:0;width:1200px;height:601px;background:linear-gradient(120deg,#2386cf,#1a70b0 60%,#2180c6)}
.nav a{color:var(--white);text-decoration:none;position:absolute;white-space:nowrap;font-size:14px}
.login{left:958px;top:16px;width:88px;height:42px}
.hero-title{left:104px;top:154px;font-family:'Oswald',sans-serif;font-weight:600;font-size:49px;line-height:62px;color:var(--white);text-transform:uppercase}
.hero-text{left:104px;top:286px;width:380px;font-size:13.5px;line-height:26px;color:var(--white)}
.hero-btn{left:105px;top:376px;width:110px;height:41px;border:2px solid var(--white);color:var(--white);font-family:'Oswald',sans-serif;font-size:14px;display:flex;align-items:center;justify-content:center}
.arrow{width:18px;height:18px;border-radius:50%;background:var(--white);display:flex;align-items:center;justify-content:center}

/* services */
.services{left:0;top:1036px;width:1200px;height:628px;background:linear-gradient(180deg,#1f7bc1,#1a72b6)}
.services .heading{color:var(--white)}
.services .underline{background:var(--white);width:90px}
.svc{width:250px;height:250px}
.svc-label{position:absolute;left:0;width:100%;text-align:center;color:var(--white);font-family:'Oswald',sans-serif;font-size:18px}

.photo{display:block}

/* clients */
.clients{left:0;top:2709px;width:1200px;height:421px;background:var(--light)}
.client{top:166px;width:236px;height:98px;background:var(--white);border:1px solid #e3e6ea;display:flex;align-items:center;justify-content:center;gap:10px;font-size:27px;font-weight:600;color:#2b2b2b}
.client .mark{width:14px;height:14px;background:#2b2b2b;border-radius:50%}

/* contact */
.field{background:var(--white);box-shadow:0 1px 8px rgba(0,0,0,.12);font-size:14px;color:#555;padding:22px 22px}

/* footer */
.footer{left:0;top:3749px;width:1200px;height:409px;background:var(--footer);color:var(--white)}
.f-head{font-family:'Oswald',sans-serif;font-size:17px;text-transform:uppercase}
.f-links{font-size:13.5px;line-height:30px}
.f-icon{width:28px;height:28px;border-radius:50%;background:var(--orange);display:flex;align-items:center;justify-content:center}
.social{width:32px;height:32px;border-radius:50%;border:2px solid var(--white)}
.social.first{background:var(--orange);border-color:var(--orange)}
</style>
</head>
<body>

<!-- HERO -->
<section class="abs hero">
  <div class="abs brand" style="left:104px;top:14px">
    <span class="brand-mark" style="width:28px;height:28px"></span>
    <div style="font-size:15px">Brightwell<br>Aero Services</div>
  </div>
  <nav class="abs nav" style="left:0;top:27px;width:1200px">
    <a style="left:547px">Home</a>
    <a style="left:637px">About</a>
    <a style="left:728px">Services</a>
    <a style="left:832px">Contact US</a>
  </nav>
  <div class="btn login">LOG IN</div>

  <h1 class="abs hero-title">Quality flying is<br>safe flying</h1>
  <p class="abs hero-text">Lorem ipsum dolor sit amet, consectetur adipiscing elit, sed do eiusmod tempor incididunt ut labore et dolore magna aliqua.</p>
  <div class="abs hero-btn">GET STARTED</div>

  <svg class="abs" style="left:748px;top:74px" width="380" height="456" viewBox="0 0 380 456" role="img" aria-label="Small single-engine aircraft flying through a blue cloudy sky">
    <defs>
      <linearGradient id="sky" x1="0" y1="0" x2="1" y2="1">
        <stop offset="0" stop-color="#8fbde6"/>
        <stop offset=".5" stop-color="#d6e6f3"/>
        <stop offset="1" stop-color="#6fa6d8"/>
      </linearGradient>
    </defs>
    <path d="M230 0 L380 0 L380 300 C380 400 300 456 200 456 C90 456 0 380 0 280 C0 200 60 150 120 110 Z" fill="url(#sky)"/>
  </svg>

  <div class="abs arrow" style="left:39px;top:359px"><svg width="10" height="10" viewBox="0 0 10 10"><path d="M9 5H1M4 2L1 5l3 3" stroke="#1f7bc1" stroke-width="1.6" fill="none"/></svg></div>
  <div class="abs arrow" style="left:1164px;top:359px"><svg width="10" height="10" viewBox="0 0 10 10"><path d="M1 5h8M6 2l3 3-3 3" stroke="#1f7bc1" stroke-width="1.6" fill="none"/></svg></div>
</section>

<!-- WELCOME -->
<section class="abs center" style="left:0;top:601px;width:1200px;height:435px">
  <h2 class="heading abs" style="left:0;top:76px;width:1200px">Welcome to <span>Brightwell Aero Services</span></h2>
  <div class="abs body-text" style="left:105px;top:139px;width:990px;font-size:13.5px">
    <p>Lorem ipsum dolor sit amet, consectetur adipiscing elit, sed do eiusmod tempor incididunt ut labore et dolore magna aliqua. Ut enim ad minim veniam, quis nostrud exercitation ullamco laboris nisi ut aliquip ex ea commodo consequat. Duis aute irure dolor in reprehenderit in voluptate velit esse cillum dolore eu fugiat nulla pariatur.Lorem ipsum dolor sit amet, consectetur adipiscing elit, sed do eiusmod tempor incididunt ut labore et dolore magna aliqua. Ut enim ad minim veniam.</p>
    <p style="margin-top:6px">Duis aute irure dolor in reprehenderit in voluptate velit esse cillum dolore eu fugiat nulla pariatur.Lorem ipsum dolor sit amet, consectetur adipiscing elit, sed do eiusmod tempor incididunt ut labore et dolore magna aliqua. Ut enim ad minim veniam.</p>
  </div>
  <div class="btn" style="left:546px;top:313px;width:118px;height:42px">READ MORE</div>
</section>

<!-- SERVICES -->
<section class="abs services center">
  <h2 class="heading abs" style="left:0;top:107px;width:1200px">Our Services<span class="underline"></span></h2>
  <p class="abs body-text" style="left:105px;top:174px;width:990px;color:#fff;font-size:13.5px">Lorem ipsum dolor sit amet, consectetur adipiscing elit, sed do eiusmod tempor incididunt ut labore et dolore magna aliqua. Ut enim ad minim veniam, quis nostrud exercitation ullamco laboris nisi ut aliquip ex ea commodo consequat.</p>

  <div class="abs svc" style="left:150px;top:257px">
    <svg width="250" height="250" viewBox="0 0 250 250" role="img" aria-label="Technician repairing an aircraft in a hangar">
      <path d="M125 6 A119 119 0 1 0 244 125" stroke="#ff6a00" stroke-width="6" fill="none"/>
      <circle cx="125" cy="125" r="112" fill="#fff"/>
      <circle cx="125" cy="125" r="106" fill="#4d4f55"/>
    </svg>
    <div class="svc-label" style="top:160px">Aircraft Repair</div>
  </div>

  <div class="abs svc" style="left:482px;top:257px">
    <svg width="250" height="250" viewBox="0 0 250 250" aria-hidden="true">
      <circle cx="125" cy="125" r="121" fill="#ff6a00"/>
      <circle cx="125" cy="125" r="112" fill="#fff"/>
      <circle cx="125" cy="125" r="106" fill="#1e1e1e"/>
    </svg>
    <div class="svc-label" style="top:66px">Small Aircraft Rental</div>
    <p class="abs" style="left:45px;top:102px;width:160px;color:#fff;font-size:10.5px;line-height:18px">Lorem ipsum dolor sit amet, consectetur adipiscing elit, sed ut labore et dolore magna aliqua.</p>
    <div class="abs" style="left:0;top:186px;width:250px;color:#2e8ad8;font-family:'Oswald',sans-serif;font-size:13px"><span style="border-bottom:1px solid #2e8ad8">Read More ⟶</span></div>
  </div>

  <div class="abs svc" style="left:813px;top:257px">
    <svg width="250" height="250" viewBox="0 0 250 250" role="img" aria-label="Flight instructor and student reviewing a checklist beside a plane">
      <path d="M244 125 A119 119 0 1 1 125 6" stroke="#ff6a00" stroke-width="6" fill="none" transform="rotate(180 125 125)"/>
      <circle cx="125" cy="125" r="112" fill="#fff"/>
      <circle cx="125" cy="125" r="106" fill="#6d7079"/>
    </svg>
    <div class="svc-label" style="top:160px">Flight School</div>
  </div>
</section>

<!-- AIRCRAFT RENTAL -->
<section class="abs" style="left:0;top:1664px;width:1200px;height:523px">
  <h2 class="heading abs" style="left:103px;top:106px">Aircraft <span>Rental</span><span class="underline"></span></h2>
  <p class="abs body-text" style="left:103px;top:172px;width:457px;text-align:justify;font-size:13.5px">Lorem ipsum dolor sit amet, consectetur adipiscing elit, sed do eiusmod tempor incididunt ut labore et dolore magna aliqua. Ut enim ad minim veniam, quis nostrud exercitation ullamco laboris nisi ut aliquip ex ea commodo consequat. Duis aute irure dolor in reprehenderit in voluptate velit esse cillum dolore eu fugiat nulla pariatur.Lorem ipsum dolor sit amet, consectetur adipiscing elit, sed do eiusmod tempor incididunt ut labore et dolore magna aliqua. Ut enim ad minim veniam, quis nostrud exercitation ullamco laboris nisi ut aliquip ex ea commodo consequat.</p>
  <div class="btn" style="left:103px;top:416px;width:118px;height:41px">READ MORE</div>
  <svg class="abs photo" style="left:599px;top:0" width="601" height="523" role="img" aria-label="Hangar interior with small aircraft parked for rental">
    <defs><linearGradient id="hg1" x1="0" y1="0" x2="0" y2="1"><stop offset="0" stop-color="#6b6a66"/><stop offset=".55" stop-color="#b3b0aa"/><stop offset="1" stop-color="#8a8680"/></linearGradient></defs>
    <rect width="601" height="523" fill="url(#hg1)"/>
  </svg>
</section>

<!-- MAINTENANCE -->
<section class="abs" style="left:0;top:2187px;width:1200px;height:522px">
  <svg class="abs photo" style="left:0;top:0" width="599" height="522" role="img" aria-label="Aircraft undergoing maintenance inside a hangar">
    <defs><linearGradient id="hg2" x1="0" y1="0" x2="1" y2="1"><stop offset="0" stop-color="#75746f"/><stop offset=".5" stop-color="#a9a6a0"/><stop offset="1" stop-color="#d2d0cc"/></linearGradient></defs>
    <rect width="599" height="522" fill="url(#hg2)"/>
  </svg>
  <h2 class="heading abs" style="left:641px;top:106px">Maintenance <span>and Repairs</span><span class="underline"></span></h2>
  <p class="abs body-text" style="left:641px;top:172px;width:455px;text-align:justify;font-size:13.5px">Lorem ipsum dolor sit amet, consectetur adipiscing elit, sed do eiusmod tempor incididunt ut labore et dolore magna aliqua. Ut enim ad minim veniam, quis nostrud exercitation ullamco laboris nisi ut aliquip ex ea commodo consequat. Duis aute irure dolor in reprehenderit in voluptate velit esse cillum dolore eu fugiat nulla pariatur.Lorem ipsum dolor sit amet, consectetur adipiscing elit, sed do eiusmod tempor incididunt ut labore et dolore magna aliqua. Ut enim ad minim veniam, quis nostrud exercitation ullamco laboris nisi ut aliquip ex ea commodo consequat.</p>
  <div class="btn" style="left:641px;top:416px;width:118px;height:41px">READ MORE</div>
</section>

<!-- CLIENTS -->
<section class="abs clients center">
  <h2 class="heading abs" style="left:0;top:76px;width:1200px">Our <span>Clients</span><span class="underline"></span></h2>
  <div class="abs client" style="left:103px">Harlan</div>
  <div class="abs client" style="left:355px;box-shadow:0 2px 10px rgba(0,0,0,.12)">Vantorcraft</div>
  <div class="abs client" style="left:607px"><span class="mark"></span>Delkin</div>
  <div class="abs client" style="left:859px">Ralstead</div>
</section>

<!-- CONTACT -->
<section class="abs center" style="left:0;top:3130px;width:1200px;height:619px">
  <h2 class="heading abs" style="left:0;top:82px;width:1200px">Get <span>in Touch</span><span class="underline"></span></h2>
  <div class="abs field" style="left:103px;top:166px;width:454px;height:63px;text-align:left">Your Name*</div>
  <div class="abs field" style="left:103px;top:250px;width:454px;height:63px;text-align:left">Phone*</div>
  <div class="abs field" style="left:103px;top:334px;width:454px;height:63px;text-align:left">Email Address *</div>
  <div class="abs field" style="left:103px;top:418px;width:454px;height:112px;text-align:left">Subject</div>
  <div class="abs field" style="left:586px;top:166px;width:509px;height:294px;text-align:left">Your Message*</div>
  <div class="btn" style="left:586px;top:488px;width:118px;height:42px">SUBMIT</div>
</section>

<!-- FOOTER -->
<footer class="abs footer">
  <div class="abs brand" style="left:96px;top:116px">
    <span class="brand-mark" style="width:40px;height:40px"></span>
    <div style="font-size:19px">Brightwell<br>Aero Services</div>
  </div>
  <div class="abs social first" style="left:105px;top:193px" aria-label="Social profile"></div>
  <div class="abs social" style="left:146px;top:193px" aria-label="Social profile"></div>
  <div class="abs social" style="left:187px;top:193px" aria-label="Social profile"></div>
  <div class="abs social" style="left:228px;top:193px" aria-label="Social profile"></div>

  <div class="abs" style="left:418px;top:96px">
    <div class="f-head">Quick Links</div>
    <div class="f-links" style="margin-top:8px">Home<br>About<br>Services<br>Contact Us</div>
  </div>

  <div class="abs" style="left:577px;top:96px;width:230px">
    <div class="f-head">Contact Us</div>
    <div class="abs f-icon" style="left:0;top:44px"><svg width="12" height="14" viewBox="0 0 12 14"><path d="M6 0a5 5 0 0 0-5 5c0 4 5 9 5 9s5-5 5-9a5 5 0 0 0-5-5zm0 7a2 2 0 1 1 0-4 2 2 0 0 1 0 4z" fill="#fff"/></svg></div>
    <div class="abs" style="left:40px;top:42px;font-size:11px;line-height:19px;width:190px"><b>Location :</b><br>39 Brightwell Aero<br>Services Lorem ipsum 250</div>
    <div class="abs f-icon" style="left:0;top:110px"><svg width="13" height="13" viewBox="0 0 13 13"><path d="M3 1l2 3-1.3 1.3a8 8 0 0 0 4 4L9 8l3 2-1 2.4C6 13 0 7 .6 2z" fill="#fff"/></svg></div>
    <div class="abs" style="left:40px;top:108px;font-size:11px;line-height:19px"><b>Phone :</b><br>+1 555 014 2270</div>
    <div class="abs f-icon" style="left:0;top:162px"><svg width="13" height="10" viewBox="0 0 13 10"><rect width="13" height="10" fill="#fff"/><path d="M0 0l6.5 5L13 0" stroke="#ff6a00" fill="none"/></svg></div>
    <div class="abs" style="left:40px;top:160px;font-size:11px;line-height:19px"><b>Email:</b><br>info@brightwellaero.com</div>
  </div>

  <div class="abs" style="left:820px;top:98px;width:250px">
    <div class="f-head">Newsletter</div>
    <p style="font-size:12px;line-height:22px;margin-top:12px">Join our mailing list to learn about our Services</p>
  </div>
  <div class="abs" style="left:820px;top:187px;width:277px;height:45px;border:1.5px solid #fff;font-size:12px;padding:14px 16px">Enter your email here*</div>
  <div class="btn" style="left:822px;top:247px;width:118px;height:42px">SUBMIT</div>

  <div class="abs" style="left:0;top:353px;width:1200px;text-align:center;font-size:13px">©2023 Brightwell Aero Services | All Rights Reserved | Terms &amp; Conditions</div>
  <div class="abs" style="left:1064px;top:356px;font-size:10px">C49</div>
</footer>

</body>
</html>
```